Business Card design project for new family-run construction business

We need a logo and business card designed for a new construction company. We want to convey a professional, but approachable image. We hope to be servicing small residential clients as well as large commercial contracts as well.
Our business will employ a single "Hydro excavator" truck, which can be used for multiple purposes: vacuuming up dirt or water, digging holes, clearing sewer blockages and so on.
We are open to different colour schemes, however blue and white, or yellow/green would be good combinations. We are open to multiple colours (2-4), so long as they are complimentary.

EDIT: Let's not put much emphasis on the octopus... unless it's very clear that the arms are actual vacuum hoses, it won't make sense. An octopus on it's own has little to do with our business.

Please also do not use actual photos of hydro-vac trucks. This is not the aesthetic we are going for.

**The logo should instead be: A stylized outline of a hydrovac truck (a line drawing or digital version of a line-drawing). See the two examples in the attached images of hydrovac trucks. I've also included a very crude pen outline as a reference. Please use your artistic discretion and talent (as I clearly have none) to make something that looks much nicer. Thanks for your efforts!**

The front of the card should have the following elements:
Logo
Name: R & T Hydro Excavation and Flushign
Two phone numbers: Direct and Office
Email address
Website
It should also have the name of the employee and their job title
At the bottom of the card it should say (in a noticeable way): "24/7 Emergency Calls Welcome"

The back of the card should have the following elements:
"20 Years Experience"
"A Canadian Family Run Business"
A small maple-leaf logo that is in a similar style to the rest of the card/logos in the bottom right corner of the back of the card. (see attached)

**We have just added a number of business card designs that really appeal to us to offer inspiration.**

Reason: We have not received designs that hit the mark of what we are looking for. Feedback has been posted, so we would like to provide the designers more time.

Target Market(s)

Commercial and residential customers. As big as large malls and office buildings, as small single-family home owners

Industry/Entity Type

Construction Company

Contact Information for Business Card

We have just added a number of business card designs that really appeal to us to offer inspiration.

Logo
Email address
Website

"20 Years Experience"

Logo Text

R & T Hydro Excavation and Flushing

Font styles to use
Serif
Sans Serif
Other font styles liked:
• Helvetica, Futura, Impact, bold strong, modern fonts that convey a sense of design and style

Colors
0592cd
ec1f27
9bcb3c

Requirements
Must have
• The front of the card should have the following elements:
• Logo
• Name: R & T Hydro Excavation and Flushign
• Two phone numbers: Direct and Office
• Email address
• Website
• It should also have the name of the employee and their job title
• At the bottom of the card it should say (in a noticeable way): "24/7 Emergency Calls Welcome"
• The back of the card should have the following elements:
• "20 Years Experience"
• "A Canadian Family Run Business"
• A small maple-leaf logo that is in a similar style to the rest of the card/logos in the bottom right corner of the back of the card. (see attached)
Nice to have
• The card does not have to be a perfect rectangle. We are open to rounded corners or cut out elements.
• Also embossing, engraving, adding highlighted/glossy layers (spot glass?), or any other effect that will give the card a unique look/feel is more than welcome.
• We would love to have a card that stands out from others and is compelling to look at it, so we are happy to incorporate any sort of modern printing technology to bring out the design.
• Please feel encouraged to be creative and design something unique, especially for this industry.
• Our dream would be if a Scandinavian architect were to go into the construction business and design this business card ;)
Should not have
• Photographs

```html
<!DOCTYPE html>
<html lang="en">
<head>
<meta charset="utf-8">
<title>R &amp; T Hydro Excavation and Flushing – Business Card</title>
<link rel="stylesheet" href="https://fonts.googleapis.com/css2?family=Arimo:wght@400;700&display=swap">
<style>
  :root {
    --page-bg: #4a4a4a;
    --card-bg: #1c1c1d;
    --brand-blue: #1ea0dc;
    --text-light: #d8d8d8;
    --text-muted: #a9a9a9;
    --rule-white: #f2f2f2;
  }
  * { box-sizing: border-box; margin: 0; padding: 0; }
  html, body {
    width: 801px; height: 1200px; overflow: hidden;
    background: var(--page-bg);
    font-family: "Arimo", Helvetica, Arial, sans-serif;
  }
  .sheet {
    width: 801px; height: 1200px;
    display: flex; flex-direction: column; align-items: center; justify-content: space-around;
    padding: 60px 0;
  }
  .card {
    position: relative;
    width: 700px; height: 400px;
    background: var(--card-bg);
    border-radius: 16px;
    overflow: hidden;
  }

  /* Company name (plain text in place of a mark) */
  .brand {
    display: flex; align-items: center; gap: 14px;
  }
  .brand-mark {
    flex: none; width: 18px; height: 18px; border-radius: 50%;
    background: var(--brand-blue);
  }
  .brand-name {
    color: var(--brand-blue); font-weight: 400; line-height: 1.25;
  }

  /* Back side */
  .card-back .brand {
    position: absolute; left: 0; right: 0; top: 120px;
    justify-content: center;
  }
  .card-back .brand-name { font-size: 28px; }
  .card-back .tagline {
    position: absolute; left: 0; right: 0; top: 220px;
    text-align: center; color: var(--brand-blue);
    font-size: 30px; line-height: 1.3;
  }

  /* Front side */
  .emergency-band {
    position: absolute; left: 0; top: 0; bottom: 0; width: 62px;
    background: var(--brand-blue);
    display: flex; align-items: center; justify-content: center;
  }
  .emergency-band span {
    transform: rotate(-90deg); white-space: nowrap;
    color: #fff; font-size: 19px; letter-spacing: .5px;
  }
  .band-rule {
    position: absolute; left: 72px; top: 0; bottom: 0; width: 4px;
    background: var(--rule-white);
  }
  .employee {
    position: absolute; left: 110px; top: 48px;
  }
  .employee-name {
    color: var(--brand-blue); font-size: 18px; font-weight: 700; letter-spacing: 1px;
  }
  .employee-title { color: var(--text-muted); font-size: 14px; margin-top: 4px; }
  .contact {
    position: absolute; left: 110px; top: 190px;
    color: var(--text-light); font-size: 17px; line-height: 1.45;
  }
  .contact .address { margin-bottom: 8px; }
  .contact ul { list-style: none; }
  .contact li { display: flex; align-items: center; gap: 10px; }
  .contact svg { width: 16px; height: 16px; flex: none; }
  .card-front .brand {
    position: absolute; left: 400px; right: 36px; top: 180px;
  }
  .card-front .brand-name { font-size: 24px; }
</style>
</head>
<body>
<main class="sheet">

  <section class="card card-back" aria-label="Card back">
    <div class="brand">
      <span class="brand-mark"></span>
      <span class="brand-name">R &amp; T Hydro Excavation and Flushing</span>
    </div>
    <p class="tagline">20 Years Experience<br>A Canadian Family Run Business</p>
  </section>

  <section class="card card-front" aria-label="Card front">
    <div class="emergency-band"><span>24/7 Emergency Calls Welcome</span></div>
    <div class="band-rule"></div>

    <div class="employee">
      <p class="employee-name">EMPLOYEE NAME</p>
      <p class="employee-title">Title</p>
    </div>

    <div class="contact">
      <p class="address">42nd Ave NW Suite 210,<br>Kelmont USA 98114</p>
      <ul>
        <li>
          <svg viewBox="0 0 16 16" aria-hidden="true"><rect x="4" y="1" width="8" height="14" rx="2" fill="none" stroke="var(--brand-blue)" stroke-width="1.6"/><circle cx="8" cy="12.5" r="1" fill="var(--brand-blue)"/></svg>
          800.555.0142
        </li>
        <li>
          <svg viewBox="0 0 16 16" aria-hidden="true"><path d="M3 2h3l1.5 3.5-2 1.3a8 8 0 0 0 3.7 3.7l1.3-2L14 10v3a1 1 0 0 1-1 1A11 11 0 0 1 2 3a1 1 0 0 1 1-1z" fill="var(--brand-blue)"/></svg>
          800.555.0178
        </li>
        <li>
          <svg viewBox="0 0 16 16" aria-hidden="true"><rect x="1" y="3" width="14" height="10" rx="1.5" fill="var(--brand-blue)"/><path d="M2 4l6 5 6-5" fill="none" stroke="var(--card-bg)" stroke-width="1.4"/></svg>
          hello@rthydro.example
        </li>
        <li>
          <svg viewBox="0 0 16 16" aria-hidden="true"><circle cx="8" cy="8" r="6.5" fill="none" stroke="var(--brand-blue)" stroke-width="1.5"/><path d="M1.5 8h13M8 1.5c-3 3.5-3 9.5 0 13M8 1.5c3 3.5 3 9.5 0 13" fill="none" stroke="var(--brand-blue)" stroke-width="1.1"/></svg>
          www.rthydro.example
        </li>
      </ul>
    </div>

    <div class="brand">
      <span class="brand-mark"></span>
      <span class="brand-name">R &amp; T Hydro Excavation<br>and Flushing</span>
    </div>
  </section>

</main>
</body>
</html>
```